Dentistry Office

We want a new design for a Dentist's office website.

The theme is: "We provide high quality, state-of-the-art, dental care in a comfortable, caring environment."

The site currently has a menu on the left of the page with about 40 items on it. There is a great deal of textual content on each page, plus several illustrations.

We want to do this using CSS, so we need specifications in the CSS for all possible elements. The CSS needs to be named in a logical manner for easy use.

Every dentist on the planet seems to use lots of Flash. We don't want to because it is so distracting. We are looking for an elegant solution targeting 24-55 age group, but not excluding anyone.

The following (from another dentist's site) can give you a taste of what we want to communicate on the site:

"After 20 years of teaching dentists how to refine their technique and many years of writing textbooks, I currently devote my time to my office and the hands-on practice of dentistry. I'd like to welcome you personally to my dental practice, and I invite you to meet my highly experienced team of professionals.

"We have offered complete dental care of the highest quality since 1978. We provide Preventive Services, Tooth Whitening and Cosmetic Dentistry for a beautiful smile, Endodontics (root canal treatment) to treat painful teeth, Sedation Dentistry so you can relax, and Dental Implants to restore what is missing. We offer total care.

"Our approach to your health is simple: We use our education, experience and dedication to provide every patient with superior dental care.

"This passion for excellence is not just a goal, but a standard every member of our team holds.

"We also pride ourselves with our state of the art procedures, training and technology. This includes creating a beautiful smile using techniques that preserve as much of the original tooth as possible.

"Our abilities are renowned throughout the dental profession and I hope if you have any questions you will contact us by an e-mail note, by phone or just by dropping by."

Keep in mind the screen shape and dimensions. Your design needs to work in the normal screen proportions, regardless of how it looks when you post it here. Scrolling is OK, but the first impression needs to work.
Updates

Keep in mind that there will be about 250 words, or more, on each page.

Competitors web sites:

http://www.brindlecovedentist.example/

http://www.brindlecovedentalcare.example/

http://www.grinsbymarlowvaledental.example/

http://www.tenbyfamilydentalcare.example/

http://www.quelmardental.example/

http://www.dovrinadental.example/

We need to compete with these.

Target Market(s)

Generally adults seeking the most experienced and comfortable-to-be-with dentist.

Industry/Entity Type

Training

Requirements
Must have
• Must stand apart from other dentists.
• Must be elegant.
• Must have a horizontal menu structure across all columns, NOT a vertical that requires scrolling, no popout, pop down, etc. menus.
• We are looking for something special.
• Do not waste your time or ours putting up templates and things you have used before.
• Personally, I do not see how someone outside the US can understand the northern California dental market. But you are welcome to try.
Should not have
• Flash or graphics that move
• The look of a template
• Folksy fonts
• Looks like you used it 20 times before

```html
<!DOCTYPE html>
<html lang="en">
<head>
<meta charset="utf-8">
<title>Dentist logo title – State-of-the-art dental care</title>
<link rel="stylesheet" href="https://fonts.googleapis.com/css2?family=Noto+Sans:wght@400;700&display=swap">
<style>
  :root {
    --page-bg: #ffffff;
    --sheet-bg: #f4f4f4;
    --brand-red: #b01c1f;
    --band-red: #8a191b;
    --accent-red: #c0181c;
    --text: #3a3a3a;
    --text-soft: #7a7a7a;
    --tab-top: #fbf3f3;
    --tab-bottom: #ecdcdc;
    --crumb-gray: #dcdcdc;
    --white: #ffffff;
    --photo-a: #e9cdb4;
    --photo-b: #cfd9d2;
  }
  * { box-sizing: border-box; margin: 0; padding: 0; }
  html, body { width: 1200px; height: 900px; overflow: hidden; background: var(--page-bg); }
  body { font-family: "Noto Sans", Tahoma, sans-serif; color: var(--text); position: relative; }

  .sheet { position: absolute; left: 90px; top: 27px; width: 1020px; height: 845px; background: var(--sheet-bg); border-top: 4px solid var(--brand-red); }

  .brand { position: absolute; left: 118px; top: 92px; display: flex; align-items: center; gap: 10px; }
  .brand-mark { width: 18px; height: 18px; background: var(--brand-red); }
  .brand-name { font-size: 26px; font-weight: 700; color: #444; letter-spacing: -0.3px; }

  .search { position: absolute; left: 842px; top: 75px; width: 147px; height: 20px; border: 1px solid #cfc4c4; background: linear-gradient(#fff, #f1e6e6); }
  .search span { position: absolute; left: 8px; top: 1px; font-size: 11px; color: #9a9a9a; }
  .search svg { position: absolute; right: 4px; top: 2px; }
  .print-icon { position: absolute; left: 1006px; top: 78px; }
  .text-size { position: absolute; left: 1041px; top: 76px; color: #888; white-space: nowrap; }
  .text-size span { margin-right: 3px; }

  .main-nav { position: absolute; left: 351px; top: 145px; height: 33px; }
  .main-nav a { position: absolute; bottom: 0; height: 28px; font-size: 14px; color: #333; text-decoration: none; text-align: center; line-height: 30px; background: linear-gradient(var(--tab-top), var(--tab-bottom)); border: 1px solid #e6d6d6; border-bottom: none; }
  .main-nav a.is-active { height: 33px; background: var(--brand-red); color: var(--white); font-weight: 700; line-height: 30px; border: none; }

  .nav-band { position: absolute; left: 120px; top: 178px; width: 960px; height: 45px; background: var(--band-red); }

  .content-frame { position: absolute; left: 120px; top: 223px; width: 960px; height: 573px; background: var(--white); box-shadow: 0 6px 18px rgba(0,0,0,0.28); }

  .sidebar { position: absolute; left: 121px; top: 223px; width: 232px; height: 573px; background: var(--brand-red); }
  .sidebar-photo { position: absolute; left: 0; top: 0; width: 218px; height: 148px; border: 3px solid var(--white); background: linear-gradient(110deg, var(--photo-a), #f3e3d4 55%, var(--photo-b)); }
  .section-title { position: absolute; left: 12px; top: 165px; font-size: 13px; font-weight: 700; color: var(--white); }
  .side-menu { position: absolute; left: 0; top: 197px; width: 232px; list-style: none; }
  .side-menu li { height: 20px; font-size: 12px; color: var(--white); padding-left: 33px; position: relative; line-height: 18px; }
  .side-menu li::before { content: ""; position: absolute; left: 12px; top: 4px; border-left: 6px solid var(--white); border-top: 5px solid transparent; border-bottom: 5px solid transparent; }
  .side-submenu { list-style: none; background: linear-gradient(#f8f2f2, #fff 50%, #f3e8e8); margin: 0 9px 0 4px; }
  .side-submenu li { color: #333; padding-left: 49px; }
  .side-submenu li::before { left: 32px; border-left-color: #333; }
  .side-submenu li.is-selected { color: var(--accent-red); }
  .side-submenu li.is-selected::before { border-left-color: var(--accent-red); }

  .breadcrumb { position: absolute; left: 366px; top: 246px; width: 466px; height: 26px; }
  .breadcrumb svg { display: block; position: absolute; left: 0; top: 0; }
  .breadcrumb span { position: absolute; top: 0; height: 26px; line-height: 26px; font-size: 11.5px; color: #222; white-space: nowrap; }
  .breadcrumb .crumb-current { color: var(--white); }

  .page-title { position: absolute; left: 369px; top: 296px; font-size: 18px; font-weight: 400; color: #333; }
  .page-title em { font-style: normal; color: var(--accent-red); }
  .page-body { position: absolute; left: 370px; top: 327px; width: 671px; font-size: 11.6px; line-height: 22px; text-align: justify; }
  .page-body p { margin-bottom: 22px; }
  .page-body a { color: var(--accent-red); }

  .site-footer { position: absolute; left: 0; top: 824px; width: 1200px; font-size: 10px; color: var(--text-soft); }
  .site-footer > * { position: absolute; top: 0; white-space: nowrap; }
  .site-footer a { color: var(--text-soft); text-decoration: underline; }
  .site-footer .sep { color: var(--text-soft); }
</style>
</head>
<body>
  <div class="sheet"></div>

  <div class="brand"><span class="brand-mark"></span><span class="brand-name">Dentist logo title</span></div>

  <div class="search"><span>Search...</span>
    <svg width="14" height="14" viewBox="0 0 14 14"><circle cx="5.5" cy="5.5" r="4" fill="none" stroke="#999" stroke-width="1.6"/><line x1="8.5" y1="8.5" x2="13" y2="13" stroke="#999" stroke-width="2"/></svg>
  </div>
  <svg class="print-icon" width="18" height="16" viewBox="0 0 18 16"><rect x="4" y="1" width="10" height="5" fill="#fff" stroke="#aaa"/><rect x="1" y="5" width="16" height="7" fill="#ccc"/><rect x="4" y="10" width="10" height="5" fill="#fff" stroke="#aaa"/></svg>
  <div class="text-size"><span style="font-size:11px">a</span><span style="font-size:14px">a</span><span style="font-size:17px">a</span></div>

  <nav class="main-nav">
    <a class="is-active" style="left:0;width:70px">Home</a>
    <a style="left:75px;width:62px">Item 2</a>
    <a style="left:140px;width:70px">Item 3</a>
    <a style="left:214px;width:70px">Item 4</a>
    <a style="left:288px;width:70px">item 5</a>
    <a style="left:362px;width:70px">item 6</a>
    <a style="left:436px;width:70px">item7</a>
    <a style="left:510px;width:70px">item 8</a>
  </nav>
  <div class="nav-band"></div>

  <div class="content-frame"></div>

  <aside class="sidebar">
    <div class="sidebar-photo" role="img" aria-label="Photo of a dentist treating a patient"></div>
    <h2 class="section-title">Section title goes here</h2>
    <ul class="side-menu">
      <li>Menu title goes here</li>
      <li>Menu title goes here</li>
      <li>Menu title goes here</li>
      <li>Menu title goes here</li>
      <ul class="side-submenu">
        <li>Menu title goes here</li>
        <li class="is-selected">Menu selected title</li>
        <li>Menu title goes here</li>
      </ul>
      <li>Menu title goes here</li>
      <li>Menu title goes here</li>
      <li>Menu title goes here</li>
    </ul>
  </aside>

  <nav class="breadcrumb">
    <svg width="466" height="26" viewBox="0 0 466 26">
      <polygon points="0,0 150,0 161,13 150,26 0,26" fill="#fff"/>
      <polygon points="3,3 148,3 157,13 148,23 3,23" fill="#dcdcdc"/>
      <polygon points="152,0 303,0 314,13 303,26 152,26 163,13" fill="#fff"/>
      <polygon points="156,3 300,3 309,13 300,23 156,23 164,13" fill="#e8e8e8"/>
      <polygon points="305,0 455,0 466,13 455,26 305,26 316,13" fill="#fff"/>
      <polygon points="308,3 452,3 461,13 452,23 308,23 317,13" fill="#c0181c"/>
    </svg>
    <span style="left:16px">Home</span>
    <span style="left:176px">Parent page title</span>
    <span class="crumb-current" style="left:329px">Current page title</span>
  </nav>

  <h1 class="page-title">State-of-the-art <em>dental care</em> page title goes here</h1>
  <main class="page-body">
    <p>Lorem ipsum dolor sit amet, consectetur adipiscing elit. Etiam consectetur velit in nisi sodales in pellentesque odio scelerisque. Vestibulum et velit id risus rutrum molestie. Phasellus vulputate est in tellus elementum eu vulputate neque tincidunt. Fusce et pretium urna. Morbi bibendum elementum ultrices. Curabitur porttitor laoreet nisi sed posuere. Suspendisse potenti. Curabitur porta varius tempus. Ut molestie mattis lacinia. Vivamus convallis elit id ante mattis et semper mi cursus. Fusce gravida dapibus enim, <a href="#">nec egestas enim malesuada</a> quis. Vivamus lectus ante, facilisis vitae scelerisque vitae, mattis vel odio. Quisque nec odio nulla, a tristique felis. Nullam sem diam, adipiscing a suscipit nec, dapibus ac magna.</p>
    <p>In dictum hendrerit metus, sit amet dapibus turpis aliquet ac. In a nisl risus. Vivamus massa arcu, commodo et varius nec, elementum id arcu. Maecenas volutpat aliquam lectus, ac imperdiet urna malesuada et. Aliquam erat volutpat. Duis semper condimentum rhoncus. Vivamus hendrerit tortor quis est egestas in varius elit malesuada. Duis ac nunc id turpis interdum lacinia vitae vel magna. Pellentesque ac venenatis purus. Suspendisse scelerisque, augue hendrerit vehicula tempus, ante elit porta risus, in tristique lectus orci ac turpis. Maecenas sollicitudin leo in massa consectetur id sollicitudin orci mollis. Sed at turpis at enim fringilla eleifend at hendrerit ipsum. Praesent aliquam dolor ac nibh auctor pellentesque vehicula leo venenatis. Nulla facilisi.</p>
    <p>Aliquam quam nisl, interdum sed varius luctus, aliquam in ipsum. Ut at sapien massa. Sed condimentum, metus sit amet placerat egestas, est felis tempor metus, ac tincidunt erat odio at tellus. Pellentesque aliquet risus et est euismod mollis. Suspendisse potenti. Donec eros augue, congue quis ullamcorper ut, pretium eget urna. Nulla semper</p>
  </main>

  <footer class="site-footer">
    <span style="left:129px">(c) Copyright 2010 Companyname.</span>
    <a style="left:357px">home</a>
    <span class="sep" style="left:404px">|</span>
    <a style="left:432px">contact</a>
    <span class="sep" style="left:491px">|</span>
    <a style="left:516px">privacy verklaring</a>
    <span class="sep" style="left:625px">|</span>
    <a style="left:647px">sitemap</a>
    <svg style="left:848px;top:2px" width="11" height="9" viewBox="0 0 11 9"><path d="M0 3 Q5.5 -1 11 3 L9 4 L8 2.5 L3 2.5 L2 4 Z M2 5 L9 5 L10 9 L1 9 Z" fill="#999"/></svg>
    <span style="left:865px">123 123123400</span>
    <span style="left:952px">info@domainname.com</span>
  </footer>
</body>
</html>
```